Telecommunications/Power civil contractor needs business card design

Were a new telecommunications/power underground civil contractor that is looking for a new business card design. Our company colours are silver or grey and orange. Feel free to use the white background logo or the black background logo.

Target Market(s)

Local contractors, utility companies, private sector mining/energy companies, developers.

Industry/Entity Type

Telecommunications

Contact Information for Business Card

Each card will need the following info:
Persons name:
Title:
E-mail:
Phone number:
Shop Address:
Mailing Address:

Requirements
Must have
• Each card will need the following info:
• Persons name:
• Title:
• E-mail:
• Phone number:
• Shop Address:
• Mailing Address:

```html
<!DOCTYPE html>
<html lang="en">
<head>
<meta charset="utf-8">
<title>Torvane Contracting Inc — Business Card</title>
<link href="https://fonts.googleapis.com/css2?family=Roboto:wght@400;700;900&display=swap" rel="stylesheet">
<style>
  :root {
    --stage: #d9d6d1;
    --card-white: #ffffff;
    --card-black: #141414;
    --orange: #f15a24;
    --grey: #6d6e71;
    --grey-light: #9a9b9e;
    --ink: #4a4a4a;
  }
  * { margin: 0; padding: 0; box-sizing: border-box; }
  html, body {
    width: 1200px; height: 675px; overflow: hidden;
    background: var(--stage);
    font-family: "Roboto", Arial, sans-serif;
  }
  .stage { position: relative; width: 1200px; height: 675px; }
  .card {
    position: absolute; top: 192px;
    width: 510px; height: 291px;
    box-shadow: 0 6px 16px rgba(0,0,0,0.25);
    overflow: hidden;
  }
  .card--front { left: 60px; background: var(--card-white); }
  .card--back { left: 630px; background: var(--card-black); }

  .brand { position: absolute; text-align: center; }
  .brand__mark {
    display: block; margin: 0 auto 8px;
    width: 62px; height: 62px; border-radius: 50%;
    border: 5px solid var(--orange);
  }
  .brand__name {
    font-weight: 900; line-height: 1; letter-spacing: 0.5px;
    text-transform: uppercase;
  }
  .brand__name span { display: block; }
  .card--front .brand { left: 30px; top: 38px; width: 200px; }
  .card--front .brand__name { color: var(--grey); font-size: 25px; }
  .card--front .brand__name span + span { font-size: 15.5px; margin-top: 3px; }

  .divider {
    position: absolute; left: 252px; top: 48px;
    width: 1px; height: 150px; background: var(--grey-light);
  }
  .details {
    position: absolute; left: 275px; top: 48px;
    color: var(--ink); font-size: 13px; line-height: 1.35;
  }
  .details__name { color: var(--orange); font-weight: 700; }
  .details__title { margin-bottom: 12px; }
  .details__address { margin-bottom: 10px; }
  .details__line { display: flex; align-items: center; gap: 6px; }
  .details__line svg { width: 11px; height: 11px; flex: none; }

  .rule {
    position: absolute; left: 0; right: 0; top: 218px;
    height: 5px; background: var(--grey);
  }
  .band {
    position: absolute; left: 0; right: 0; top: 231px; bottom: 0;
    background: var(--orange);
  }

  .card--back .brand { left: 0; right: 0; top: 78px; }
  .card--back .brand__mark { width: 74px; height: 74px; border-width: 6px; }
  .card--back .brand__name { color: var(--grey-light); font-size: 32px; }
  .card--back .brand__name span + span { font-size: 19px; margin-top: 4px; }
</style>
</head>
<body>
<main class="stage">
  <section class="card card--front">
    <div class="brand">
      <span class="brand__mark"></span>
      <p class="brand__name"><span>Torvane</span><span>Contracting Inc</span></p>
    </div>
    <div class="divider"></div>
    <div class="details">
      <p class="details__name">Marla Quinlan</p>
      <p class="details__title">Managing Director</p>
      <p class="details__address">Torvane Contracting Inc<br>N. 8 Harbor Lane,<br>Suite 210, Fairmont, WA 55010</p>
      <p class="details__line">
        <svg viewBox="0 0 12 12" aria-hidden="true"><path fill="#f15a24" d="M2.5 1h2l1 2.8-1.3 1a6 6 0 0 0 2.9 2.9l1-1.3 2.9 1v2C11 10.3 10.3 11 9.5 11 5 11 1 7 1 2.5 1 1.7 1.7 1 2.5 1z"/></svg>
        555.204.318
      </p>
      <p class="details__line">
        <svg viewBox="0 0 12 12" aria-hidden="true"><rect x="1" y="2.5" width="10" height="7" rx="1" fill="#f15a24"/><path d="M1.5 3l4.5 3.5L10.5 3" stroke="#fff" stroke-width="1" fill="none"/></svg>
        info@torvanecontracting.com
      </p>
    </div>
    <div class="rule"></div>
    <div class="band"></div>
  </section>

  <section class="card card--back">
    <div class="brand">
      <span class="brand__mark"></span>
      <p class="brand__name"><span>Torvane</span><span>Contracting Inc</span></p>
    </div>
  </section>
</main>
</body>
</html>
```